Design for a 4 screens iOS and Android app - "VelaTrakko"

The app allows you to track your car gasoline refill ...
We need a design for the 4 screens of the app:
a) 1 form with 3 fields.
b) 1 simple list view
c) 1 summary view
d) 1 text page
2 "alerts" items are also to be designed.
No specific guidelines, nor logo or whatever.
It will be a free app distributed on iOS and Androïd.
We just want to make it looking nice & very usable for end users.
Target Market(s)
B2C app
Industry/Entity Type
Android

```html
<!DOCTYPE html>
<html lang="en">
<head>
<meta charset="UTF-8">
<title>VelaTrakko</title>
<link href="https://fonts.googleapis.com/css2?family=Roboto:ital,wght@0,300;0,400;1,300&display=swap" rel="stylesheet">
<style>
  :root {
    --status-bar: #10324a;
    --app-bar: #1e6a8e;
    --snackbar: #33a0bf;
    --gold-dark: #c4860a;
    --gold-mid: #d49f0c;
    --gold-light: #e6c20b;
    --fab: #1d6a8c;
    --nav-bar: #000000;
    --on-dark: #ffffff;
    --nav-icon: #e6e6e6;
  }
  * { box-sizing: border-box; margin: 0; padding: 0; }
  html, body { width: 675px; height: 1200px; overflow: hidden; background: #fff; }
  body { font-family: 'Roboto', sans-serif; color: var(--on-dark); }

  .screen { position: relative; width: 675px; height: 1200px; overflow: hidden; }

  .status-bar {
    position: absolute; top: 0; left: 0; width: 675px; height: 45px;
    background: var(--status-bar);
  }
  .status-bar svg { position: absolute; top: 0; left: 0; }
  .status-time {
    position: absolute; right: 14px; top: 10px;
    font-size: 22px; font-weight: 400; letter-spacing: 0.3px;
  }

  .app-bar {
    position: absolute; top: 45px; left: 0; width: 675px; height: 88px;
    background: var(--app-bar);
    box-shadow: 0 3px 5px rgba(0,0,0,0.35);
    z-index: 2;
  }
  .app-title {
    position: absolute; left: 138px; top: 22px;
    font-size: 35px; font-weight: 400; letter-spacing: 0.2px;
  }
  .app-bar svg { position: absolute; }

  .snackbar {
    position: absolute; top: 133px; left: 0; width: 675px; height: 88px;
    background: var(--snackbar);
  }
  .snackbar svg { position: absolute; }
  .snackbar-text {
    position: absolute; left: 138px; top: 32px;
    font-size: 20px; font-weight: 400; letter-spacing: 0.4px;
  }

  .meter-panel {
    position: absolute; top: 221px; left: 0; width: 675px; height: 893px;
    background:
      radial-gradient(ellipse at 40% 8%, var(--gold-dark) 0%, rgba(196,134,10,0) 45%),
      linear-gradient(215deg, var(--gold-light) 0%, var(--gold-dark) 22%, var(--gold-mid) 55%, var(--gold-light) 100%);
  }
  .meter-value {
    position: absolute; left: 0; right: 0; top: 298px;
    text-align: center;
    font-size: 102px; font-weight: 300; letter-spacing: -1px;
    line-height: 1.2;
  }
  .meter-unit { margin-left: 26px; font-weight: 300; }

  .fab {
    position: absolute; left: 506px; top: 715px; width: 135px; height: 135px;
    border-radius: 50%; background: var(--fab);
    box-shadow: 0 5px 9px rgba(0,0,0,0.35);
  }
  .fab svg { position: absolute; left: 40px; top: 40px; }

  .nav-bar {
    position: absolute; top: 1114px; left: 0; width: 675px; height: 86px;
    background: var(--nav-bar);
  }
  .nav-bar svg { position: absolute; top: 0; left: 0; }
</style>
</head>
<body>
<main class="screen">

  <div class="status-bar">
    <svg width="675" height="45" viewBox="0 0 675 45" aria-hidden="true">
      <path d="M462 9 a9 9 0 0 1 9 9 c0 7 -9 16 -9 16 c0 0 -9 -9 -9 -16 a9 9 0 0 1 9 -9z" fill="#fff"/>
      <circle cx="462" cy="18" r="3.5" fill="var(--status-bar)"/>
      <path d="M486 14 a33 33 0 0 1 44 0 L508 36 Z" fill="#fff"/>
      <path d="M549 36 L549 11 L524 36 Z" fill="#fff"/>
      <rect x="567" y="9" width="14" height="27" rx="1" fill="#fff"/>
      <rect x="571" y="6" width="6" height="4" fill="#fff"/>
    </svg>
    <span class="status-time">10:55</span>
  </div>

  <header class="app-bar">
    <svg class="menu-icon" style="left:34px;top:33px" width="34" height="24" viewBox="0 0 34 24" aria-label="Menu" role="img">
      <rect y="0" width="34" height="3.5" fill="#fff"/>
      <rect y="10" width="34" height="3.5" fill="#fff"/>
      <rect y="20" width="34" height="3.5" fill="#fff"/>
    </svg>
    <h1 class="app-title">VelaTrakko</h1>
    <svg class="chart-icon" style="left:590px;top:22px" width="52" height="42" viewBox="0 0 52 42" aria-label="Statistics" role="img">
      <path d="M2 2 V40 H50" fill="none" stroke="#fff" stroke-width="3"/>
      <path d="M6 33 L18 19 L32 26 L47 8" fill="none" stroke="#fff" stroke-width="3"/>
      <circle cx="18" cy="19" r="3.5" fill="#fff"/>
      <circle cx="32" cy="26" r="3.5" fill="#fff"/>
      <circle cx="47" cy="8" r="3.5" fill="#fff"/>
    </svg>
  </header>

  <div class="snackbar">
    <svg style="left:33px;top:38px" width="36" height="28" viewBox="0 0 36 28" aria-hidden="true">
      <path d="M3 14 L13 24 L33 3" fill="none" stroke="#fff" stroke-width="3.5"/>
    </svg>
    <span class="snackbar-text">ENTRY SAVED</span>
  </div>

  <section class="meter-panel">
    <p class="meter-value">129,000<span class="meter-unit">ℓ</span></p>
    <div class="fab" role="button" aria-label="Add entry">
      <svg width="55" height="55" viewBox="0 0 55 55" aria-hidden="true">
        <rect x="24.5" y="4" width="6" height="47" fill="#fff"/>
        <rect x="4" y="24.5" width="47" height="6" fill="#fff"/>
      </svg>
    </div>
  </section>

  <nav class="nav-bar">
    <svg width="675" height="86" viewBox="0 0 675 86" aria-hidden="true">
      <path d="M161 33 L137 46 L161 59 Z" fill="none" stroke="var(--nav-icon)" stroke-width="3" stroke-linejoin="round"/>
      <circle cx="338" cy="46" r="14" fill="none" stroke="var(--nav-icon)" stroke-width="3"/>
      <rect x="513" y="32" width="28" height="28" rx="2" fill="none" stroke="var(--nav-icon)" stroke-width="3"/>
    </svg>
  </nav>

</main>
</body>
</html>
```